Therapy Services & Training

I provide counseling/therapy to individuals and families. I also travel the country and provide training at conferences.
I would like to see a card which takes my company name and design a logo using the letters "HCAL".
Target Market(s)
Therapists, non-profit organizations, clients looking for therapy
Industry/Entity Type
Training
Contact Information for Business Card
Harborstone Clinical Advising & Learning LLC
Dana Pellham, M.S.W., LCSW
Clinical Therapist & Trainer
Providing clinical therapy services to individuals, families, couples & children. We also provide life coaching and crisis training.
counselordana@mailbrook.example
www.harborstoneclinicaladvising.example
(555) 214-3097
Alder Falls, IL 60999
(BACK SIDE OF CARD)
We are certified by the Baseline Ongoing Bar Studies (BOBS) Panel of the Prairie State High Tribunal to provide Continuing Legal Education (CLE) credits to Illinois attorneys. Call about what courses we offer! (555) 214-3097

```html
<!DOCTYPE html>
<html lang="en">
<head>
<meta charset="utf-8">
<title>Harborstone Clinical Advising &amp; Learning LLC – Business Card</title>
<link rel="stylesheet" href="https://fonts.googleapis.com/css2?family=Mulish:wght@300;400;500;700&display=swap">
<style>
  :root {
    --backdrop: #eef0e6;
    --card: #ffffff;
    --ink: #111111;
    --violet: #3a12e6;
    --sky: #2f8cf2;
    --lavender: #b497f0;
    --soft-blue: #4a86d8;
  }
  * { box-sizing: border-box; margin: 0; padding: 0; }
  html, body {
    width: 1200px; height: 1000px; overflow: hidden;
    background: var(--backdrop);
    font-family: "Mulish", "Helvetica Neue", Arial, sans-serif;
  }
  .sheet {
    position: relative; width: 1200px; height: 1000px;
  }
  .card {
    position: absolute; left: 215px;
    width: 770px; height: 440px;
    background: var(--card);
    box-shadow: 0 2px 10px rgba(0,0,0,0.12);
  }
  .card--front { top: 36px; }
  .card--back { top: 524px; }

  /* Front */
  .company-name {
    position: absolute; left: 52px; top: 46px;
    font-size: 28px; font-weight: 400; line-height: 1.25; color: var(--ink);
  }
  .brand-mark {
    position: absolute; display: flex; align-items: center; gap: 12px;
    color: var(--violet); font-weight: 700;
  }
  .card--front .brand-mark { right: 56px; top: 110px; font-size: 40px; }
  .brand-dot {
    border-radius: 50%; background: var(--sky);
  }
  .card--front .brand-dot { width: 34px; height: 34px; }

  .person {
    position: absolute; left: 50px; top: 218px;
    display: flex; align-items: baseline; gap: 8px;
  }
  .person-name { font-size: 32px; font-weight: 700; color: var(--violet); }
  .person-creds { font-size: 20px; font-weight: 500; color: var(--ink); }

  .contact {
    position: absolute; left: 52px; top: 292px;
    font-size: 16px; line-height: 21px; color: var(--sky);
  }
  .contact-role { color: var(--ink); font-weight: 500; }

  .tagline {
    position: absolute; right: 56px; top: 304px;
    text-align: right; font-size: 15.5px; font-weight: 300;
    line-height: 29px; color: var(--soft-blue);
  }

  /* Back */
  .back-copy {
    position: absolute; left: 56px; top: 62px; width: 560px;
    font-size: 17px; font-weight: 300; line-height: 27px; color: var(--soft-blue);
  }
  .back-copy p + p { margin-top: 28px; }
  .card--back .brand-mark { right: 60px; bottom: 70px; font-size: 58px; }
  .card--back .brand-dot { width: 48px; height: 48px; }
</style>
</head>
<body>
<main class="sheet">
  <section class="card card--front" aria-label="Business card front">
    <h1 class="company-name">Harborstone Clinical<br>Advising &amp; Learning LLC</h1>
    <div class="brand-mark"><span class="brand-dot"></span><span>HCAL</span></div>
    <div class="person">
      <span class="person-name">Dana Pellham</span>
      <span class="person-creds">M.S.W., LCSW</span>
    </div>
    <div class="contact">
      <div class="contact-role">Clinical Therapist &amp; Trainer</div>
      <div>counselordana@mailbrook.example</div>
      <div>www.harborstoneclinicaladvising.example</div>
      <div>(555) 214-3097</div>
      <div>Alder Falls, IL 60999</div>
    </div>
    <p class="tagline">Providing clinical therapy services to<br>individuals, families, couples, and children.<br>We also provide life coaching and crisis training.</p>
  </section>

  <section class="card card--back" aria-label="Business card back">
    <div class="back-copy">
      <p>We are certified by the Baseline Ongoing Bar Studies (BOBS) Panel of the Prairie State High Tribunal to provide Continuing Legal Education (CLE) credits to Illinois attorneys.</p>
      <p>Call about what courses we offer! (555) 214-3097</p>
    </div>
    <div class="brand-mark"><span class="brand-dot"></span><span>HCAL</span></div>
  </section>
</main>
</body>
</html>
```